Velmarsh Group Webpage Design

We need a new website for our company. The company is Velmarsh Group Pty Ltd. We are in the business of Asbestos Removal; Demolition; Earthworks and Transport. We do not advertise and would like our website to be a reference point for our clients / potential clients and also to make our services known to those searching the internet for the services we offer. Some examples of the style of website we are after are:
http://www.quarnedemolition-example.com.au/
http://m.brintowerdemolitions-example.com.au/
http://www.fenwarddemolition-example.com.au
http://www.tolvik-example.com.au
http://www.ptrservices-example.com.au
http://www.steadfast-dismantling-example.com.au
We will need to work on content. Enclosed is an example. We also need to purchase the domain velmarshgroup-example.com.au and need to set up email accounts and ensure the website is mobile friendly. We have a company logo and have built our business on delivering professional, quality services on time. We would like the webpage to be simple, informative and professional - black and white / grey themed. We would also like to add a photo gallery etc later.

Industry/Entity Type

Construction

Coding

Coded - Design and coding required

Number of Pages Required

1 page

Colors
000000
fcfcfc
959595
dddddd

Requirements
Must have
• Information regarding the services we provide

```html
<!DOCTYPE html>
<html lang="en">
<head>
<meta charset="utf-8">
<title>Velmarsh Group</title>
<link rel="stylesheet" href="https://fonts.googleapis.com/css2?family=Exo+2:wght@400;500&family=Open+Sans:wght@400;600;700&display=swap">
<style>
:root{
  --black:#000000;
  --white:#fcfcfc;
  --grey:#959595;
  --light:#dddddd;
  --text:#444444;
  --footer:#111111;
  --footer-base:#050505;
}
*{box-sizing:border-box;margin:0;padding:0}
html,body{width:1200px;height:4478px;overflow:hidden}
body{background:var(--white);font-family:"Open Sans",Arial,sans-serif;color:var(--text);font-size:15px;line-height:1.6;position:relative}
.display{font-family:"Exo 2",Arial,sans-serif;font-weight:400;color:#111}
section,header,footer{position:absolute;left:0;width:1200px}

.site-header{top:0;height:113px;background:rgba(252,252,252,.88);z-index:2;display:flex;align-items:center;justify-content:space-between;padding:0 75px 0 78px}
.brand{font-family:"Exo 2",Arial,sans-serif;font-weight:500;font-size:40px;letter-spacing:3px;color:#333;text-transform:uppercase}
.nav{display:flex;gap:6px;list-style:none}
.nav a{display:block;padding:12px 16px;font-size:17px;text-transform:uppercase;color:#111;text-decoration:none;font-weight:600}
.nav a.active{background:var(--black);color:var(--white)}

.hero{top:0;height:800px;background:linear-gradient(180deg,#2f77b8 0%,#8cbde3 35%,#e9e2c6 58%,#a67a45 75%,#6e4a26 100%)}
.hero-band{top:800px;height:150px;background:var(--black);display:flex;align-items:center;justify-content:center}
.hero-band p{font-family:"Exo 2",Arial,sans-serif;color:var(--white);font-size:42px;letter-spacing:3px}

.welcome{top:950px;height:328px;text-align:center;padding:50px 80px 0}
.welcome-bg{position:absolute;inset:0;background:linear-gradient(180deg,#ececec,#e2e2e2 60%,#eeeeee);z-index:-1}
.section-title{font-size:46px;letter-spacing:1px;margin-bottom:14px}
.welcome p{font-size:14.5px;margin-bottom:22px}

.services-intro{top:1278px;height:238px;text-align:center;padding:58px 190px 0}
.services-intro p{font-size:14.5px}

.service{padding:0 78px}
.service.grey{background:var(--light)}
.service h3{font-size:34px;margin-bottom:14px}
.service p{font-size:14.5px;color:#555}
.photo{position:absolute}
.ticks{list-style:none;margin-top:14px}
.ticks li{display:flex;align-items:center;gap:12px;font-size:14px;color:#333;margin-bottom:12px}
.ticks svg{width:18px;height:18px;flex:none}

.demolition{top:1516px;height:448px}
.demolition .copy{position:absolute;left:80px;top:62px;width:487px}
.demolition .photo{left:642px;top:69px;width:478px;height:319px;background:linear-gradient(180deg,#3b7fd1 0%,#9cc6ec 45%,#b7a98a 70%,#7d7468 100%)}

.earthworks{top:1964px;height:424px}
.earthworks .photo{left:78px;top:93px;width:489px;height:271px;background:linear-gradient(180deg,#5d6f86 0%,#a8b3c0 45%,#9c8e72 72%,#6f6654 100%)}
.earthworks .copy{position:absolute;left:645px;top:80px;width:477px}
.earthworks .ticks{display:grid;grid-template-columns:1fr 1fr}

.asbestos{top:2388px;height:606px}
.asbestos .copy{position:absolute;left:80px;top:62px;width:500px}
.asbestos .copy p{font-size:14px;line-height:1.55}
.asbestos .photo{left:633px;top:167px;width:489px;height:325px;background:linear-gradient(180deg,#a9c4dc 0%,#cfdde6 30%,#7f9a5a 45%,#b6b9b8 62%,#8d9192 100%)}

.hours{top:2994px;height:206px;text-align:center;padding:50px 190px 0}
.hours h2{font-size:34px;margin-bottom:16px}
.hours p{font-size:14.5px}

.commitments{top:3200px;height:550px;display:flex;gap:63px;padding:60px 78px 0}
.commitments-bg{position:absolute;inset:0;background:linear-gradient(180deg,#c9c9c9 0%,#e4e4e4 40%,#d6d6d6 70%,#bdbdbd 100%);z-index:-1}
.commitments .col{width:502px}
.commitments .col:last-child{width:477px}
.commitments h2{font-size:44px;margin-bottom:12px}
.commitments p{font-size:14.5px;color:#333}

.quote{top:3750px;height:430px;text-align:center}
.quote h2{font-size:44px;padding-top:30px}
.field{position:absolute;background:var(--light);border:1px solid #cfcfcf;font-size:14px;color:#777;text-align:left;padding:10px 14px}
.btn{position:absolute;left:507px;top:343px;width:186px;height:50px;background:var(--black);color:var(--white);font-size:21px;font-family:"Exo 2",Arial,sans-serif;text-transform:uppercase;display:flex;align-items:center;justify-content:center;letter-spacing:1px}

.site-footer{top:4180px;height:230px;background:var(--footer);color:var(--white)}
.contact{position:absolute;top:48px}
.contact h4{font-family:"Exo 2",Arial,sans-serif;font-weight:400;font-size:23px;line-height:1.2}
.contact .role{font-size:12px;color:var(--grey);margin-bottom:16px}
.contact ul{list-style:none}
.contact li{display:flex;align-items:center;gap:18px;font-size:14px;height:36px}
.contact svg{width:18px;height:18px;fill:var(--white)}
.legal{top:4410px;height:68px;background:var(--footer-base);color:var(--grey);font-size:13px;display:flex;align-items:center;justify-content:center}
.legal strong{color:var(--white);margin:0 4px}
</style>
</head>
<body>
<svg width="0" height="0" style="position:absolute">
  <defs>
    <symbol id="tick" viewBox="0 0 18 18"><rect x="1" y="3" width="13" height="13" fill="none" stroke="#222" stroke-width="1.6"/><path d="M4 9l3.5 3.5L17 2" fill="none" stroke="#222" stroke-width="2.2"/></symbol>
    <symbol id="pin" viewBox="0 0 18 18"><path d="M9 1a6 6 0 0 0-6 6c0 4.5 6 10 6 10s6-5.5 6-10a6 6 0 0 0-6-6zm0 8.3a2.3 2.3 0 1 1 0-4.6 2.3 2.3 0 0 1 0 4.6z"/></symbol>
    <symbol id="phone" viewBox="0 0 18 18"><path d="M5 1h8a1.5 1.5 0 0 1 1.5 1.5v13A1.5 1.5 0 0 1 13 17H5a1.5 1.5 0 0 1-1.5-1.5v-13A1.5 1.5 0 0 1 5 1zm0 2v10h8V3zm4 11a1 1 0 1 0 0 2 1 1 0 0 0 0-2z"/></symbol>
    <symbol id="mail" viewBox="0 0 18 18"><path d="M1 3h16v12H1zm1.8 1.5L9 9.5l6.2-5zM2.5 6v7.5h13V6L9 11.3z"/></symbol>
  </defs>
</svg>

<section class="hero" role="img" aria-label="Yellow excavator on a dirt site under a bright blue sky"></section>

<header class="site-header">
  <div class="brand">Velmarsh Group</div>
  <ul class="nav">
    <li><a class="active" href="#">Home</a></li>
    <li><a href="#">About</a></li>
    <li><a href="#">Services</a></li>
    <li><a href="#">Safety</a></li>
    <li><a href="#">Environment</a></li>
    <li><a href="#">Contact</a></li>
  </ul>
</header>

<section class="hero-band"><p>TRANSPORT • DEMOLITION • EARTHMOVING</p></section>

<section class="welcome">
  <div class="welcome-bg" role="img" aria-label="Faded construction cranes against a pale sky"></div>
  <h1 class="section-title display">WELCOME TO VELMARSH GROUP</h1>
  <p>Velmarsh Transport Pty Ltd was established by Director Daniel Velmarsh in 2002 with a focus providing services within the transport industry. Over time the company has developed and expanded to include the provision of Earthworks and Demolition. Daniel has over 10 years' experience working at all levels within these industries focusing primarily on Demolition and Earthworks in recent times.</p>
  <p>Velmarsh Transport and Demolition is built on core values of Service, Safety and Environment and are dedicated to delivering a quality, safe, cost effective, efficient and reliable service.</p>
</section>

<section class="services-intro">
  <h2 class="section-title display">OUR SERVICES</h2>
  <p>Velmarsh Transport and Demolition offer an extensive range of services including Demolition, Earthworks and Asbestos Removal. We make it our business to consult with clients, assess their needs and tailor a complete solution. We pride ourselves on a professional approach and timely delivery of services.</p>
</section>

<section class="service grey demolition">
  <div class="copy">
    <h3 class="display">Demolition</h3>
    <p>Velmarsh Transport and Demolition provide an extensive range of demolition services. A large amount of experience across a broad range of projects results in a dependable service and peace of mind for all clients. Services include:</p>
    <ul class="ticks">
      <li><svg><use href="#tick"/></svg>Commercial Demolition</li>
      <li><svg><use href="#tick"/></svg>Infrastructure Demolition</li>
      <li><svg><use href="#tick"/></svg>Domestic Demolition</li>
      <li><svg><use href="#tick"/></svg>Partial Demolition / Strip out</li>
    </ul>
  </div>
  <div class="photo" role="img" aria-label="Excavators breaking up a concrete structure on a sunny day"></div>
</section>

<section class="service earthworks">
  <div class="photo" role="img" aria-label="Bulldozer and dump truck moving earth under a cloudy sky"></div>
  <div class="copy">
    <h3 class="display">Earthworks</h3>
    <p>Velmarsh Transport and Demolition possess all necessary equipment and skilled personnel to provide earthmoving services including:</p>
    <ul class="ticks">
      <li><svg><use href="#tick"/></svg>Deep Excavation</li>
      <li><svg><use href="#tick"/></svg>Vegetation / Tree Removal</li>
      <li><svg><use href="#tick"/></svg>Bulk Earthworks</li>
      <li><svg><use href="#tick"/></svg>Site Preparation</li>
      <li><svg><use href="#tick"/></svg>Final Trim</li>
      <li><svg><use href="#tick"/></svg>Site Remediation</li>
    </ul>
  </div>
</section>

<section class="service grey asbestos">
  <div class="copy">
    <h3 class="display">Asbestos</h3>
    <p>Asbestos is a naturally occurring silicate mineral made up of tiny fibres. When disturbed, it may produce a dust containing asbestos fibres. Breathing these fibres into the lungs may, in turn, cause a range of health problems including pleural plaques, asbestosis, lung cancer and mesothelioma.</p>
    <p>Asbestos was commonly used in building materials between the 1940s and the late 1980s. It was used because it is fire resistant, durable and an efficient insulating material. Now that we are aware of the health risks, it is no longer mined in Australia. Since the beginning of 2004, it has also not been imported or used in any Australian products.</p>
    <p>It is due to the abovementioned history of use that Asbestos now has a widespread presence in most current demolition projects. Due to its inherent and severe health risks to workers and the community, Velmarsh Transport and Demolition employ a skilled asbestos removal team to assess, monitor, remove and dispose of asbestos, contaminated and hazardous materials.</p>
  </div>
  <div class="photo" role="img" aria-label="Corrugated asbestos cement roof sheeting beside green foliage"></div>
</section>

<section class="hours">
  <h2 class="display">Hours of Operation</h2>
  <p>Velmarsh Transport and Demolition operate Monday to Saturday. Hours of operation are generally assessed and implemented to meet the needs of each individual project.</p>
</section>

<section class="commitments">
  <div class="commitments-bg" role="img" aria-label="Faded steel building framework and construction site"></div>
  <div class="col">
    <h2 class="display">Safety</h2>
    <p>The safety of our clients, workforce and wider community is of paramount importance to Velmarsh Transport and Demolition. We employ a comprehensive Safety Management System ensuring:</p>
    <ul class="ticks">
      <li><svg><use href="#tick"/></svg>A safe work environment</li>
      <li><svg><use href="#tick"/></svg>Safe plant and structures</li>
      <li><svg><use href="#tick"/></svg>Safe systems of work</li>
      <li><svg><use href="#tick"/></svg>Safe use, handling and storage – plant, structures, substances</li>
      <li><svg><use href="#tick"/></svg>Adequate resources</li>
      <li><svg><use href="#tick"/></svg>Information, training, instruction and supervision</li>
      <li><svg><use href="#tick"/></svg>Continued monitoring</li>
    </ul>
  </div>
  <div class="col">
    <h2 class="display">Environment</h2>
    <p>Velmarsh Transport &amp; Demolition is committed to reducing the environmental impact of its undertakings. Environmental considerations and deeply embedded within business culture to ensure the environment is preserved for future generations. We employ an Environmental Management System which includes / considers:</p>
    <ul class="ticks">
      <li><svg><use href="#tick"/></svg>Environmental Management Plans</li>
      <li><svg><use href="#tick"/></svg>Vegetation / Tree Protection</li>
      <li><svg><use href="#tick"/></svg>Reuse / salvage</li>
      <li><svg><use href="#tick"/></svg>Recycling</li>
    </ul>
  </div>
</section>

<section class="quote">
  <h2 class="display">Get Quote</h2>
  <div class="field" style="left:275px;top:124px;width:316px;height:45px">Enter Name</div>
  <div class="field" style="left:609px;top:124px;width:316px;height:45px">Enter Company Name</div>
  <div class="field" style="left:275px;top:184px;width:316px;height:45px">Contact No.</div>
  <div class="field" style="left:609px;top:184px;width:316px;height:45px">Email Id</div>
  <div class="field" style="left:275px;top:229px;width:650px;height:96px;margin-top:15px">Details</div>
  <div class="btn">Get Quote</div>
</section>

<footer class="site-footer">
  <div class="contact" style="left:80px">
    <h4>Daniel Velmarsh</h4>
    <div class="role">Director</div>
    <ul>
      <li><svg><use href="#pin"/></svg>PO Box 512 CEDARVALE QLD 4290</li>
      <li><svg><use href="#phone"/></svg>0400 000 141</li>
      <li><svg><use href="#mail"/></svg>vtdemolition@example.com</li>
    </ul>
  </div>
  <div class="contact" style="left:650px">
    <h4>Megan Thorley</h4>
    <div class="role">Administration</div>
    <ul>
      <li><svg><use href="#pin"/></svg>PO Box 512 CEDARVALE QLD 4290</li>
      <li><svg><use href="#phone"/></svg>0400 000 294</li>
      <li><svg><use href="#mail"/></svg>vtdemolition@example.com</li>
    </ul>
  </div>
</footer>
<div class="legal" style="position:absolute;left:0;width:1200px">© <strong>VELMARSH GROUP</strong> - 2015, All Rights Reserved.</div>
</body>
</html>
```